Chomp-iZ Salsa Website

Needing a website to promote and sell our salsa line.

Each tab at the top of our home page will be need to be clickable taking you to another page. Other pages besides the home page include: about us, recipes, buy now, events, contact us.
Updates

Our project brief has been updated to reflect more details.

Coding

Coded - Design and coding required

Number of Pages Required

5+ page

Requirements
Must have
• Follow us on Facebook and Instagram.

Buy now page will need to have option to add products to shopping chart. We have a PayLo account that will need to linked to shopping chart for payments.

```html
<!DOCTYPE html>
<html lang="en">
<head>
<meta charset="utf-8">
<title>Chomp-iZ Salsa</title>
<link href="https://fonts.googleapis.com/css2?family=Poppins:ital,wght@0,300;0,400;0,500;0,600;0,700;1,400&display=swap" rel="stylesheet">
<style>
:root{
  --red:#c0272d;
  --red-deep:#a81e24;
  --yellow:#f0b63c;
  --cream:#fdf3de;
  --ink:#1c1c1c;
  --grey:#f1f1f1;
  --black:#050505;
  --white:#ffffff;
}
*{box-sizing:border-box;margin:0;padding:0}
html,body{width:1200px;height:3785px;overflow:hidden}
body{position:relative;font-family:"Poppins",sans-serif;color:var(--ink);background:var(--white)}
.abs{position:absolute}
a{color:inherit;text-decoration:none}

.topbar{left:0;top:0;width:1200px;height:31px;background:var(--yellow);font-size:11px;font-weight:600;color:#3a2a10}
.topbar .left{position:absolute;left:114px;top:8px;word-spacing:4px}
.topbar .right{position:absolute;right:88px;top:8px}

.header{left:0;top:31px;width:1200px;height:96px;background:var(--cream)}
.brand{position:absolute;left:116px;top:28px;font-size:30px;font-weight:700;color:var(--red);letter-spacing:-0.5px}
.search{position:absolute;left:330px;top:24px;width:437px;height:49px;background:var(--white);border-radius:25px;box-shadow:0 2px 6px rgba(0,0,0,.08)}
.search span{position:absolute;left:28px;top:15px;font-size:13px;font-style:italic;color:#999}
.search b{position:absolute;right:0;top:0;width:116px;height:49px;background:var(--red);color:#fff;border-radius:0 25px 25px 0;font-size:16px;text-align:center;line-height:49px}
.call{position:absolute;left:858px;top:24px}
.call .ico{position:absolute;left:0;top:0;width:52px;height:52px;border-radius:50%;background:var(--yellow)}
.call small{position:absolute;left:65px;top:2px;font-size:13px;font-weight:600;color:var(--yellow);white-space:nowrap}
.call strong{position:absolute;left:65px;top:18px;font-size:25px;font-weight:600;color:var(--red);white-space:nowrap}

.nav{left:0;top:127px;width:1200px;height:57px;background:var(--red)}
.nav ul{list-style:none;position:absolute;left:226px;top:20px;display:flex;gap:30px;font-size:12px;font-weight:600;color:#fff}
.nav li.active{color:var(--yellow)}
.nav .social{position:absolute;left:780px;top:12px;display:flex;gap:16px}
.nav .social i{display:block;width:36px;height:36px;border-radius:50%;background:var(--yellow);position:relative}

.hero{left:0;top:184px;width:1200px;height:622px;background:linear-gradient(180deg,#8a3b2a 0%,#a8533c 40%,#5b2a20 75%,#2a2624 100%)}
.hero h1{position:absolute;left:0;width:1200px;top:110px;text-align:center;color:#fff;font-size:43px;font-weight:400;line-height:47px}
.hero .btn{position:absolute;left:503px;top:236px;width:193px;height:52px;border-radius:26px;background:var(--red);color:#fff;font-size:16px;font-weight:600;text-align:center;line-height:52px}
.hero .jars{position:absolute;left:255px;top:312px;width:680px;height:310px;border-radius:30px 30px 0 0;background:linear-gradient(180deg,#2a2420 0%,#6a2d17 40%,#3a1d10 100%)}

.perks{left:111px;top:892px;width:977px;height:178px;border:1px solid #999}
.perk{position:absolute;top:44px;width:240px;text-align:center}
.perk svg{display:block;margin:0 auto 6px}
.perk b{display:block;font-size:14px;font-weight:600}
.perk span{font-size:12px;color:#333}

.section-title{left:0;width:1200px;text-align:center;font-size:34px;font-weight:400}
.section-title b{font-weight:700}
.section-title::after{content:"";display:block;width:24px;height:4px;background:var(--red);margin:10px auto 0}

.card{position:absolute;width:264px;height:363px;background:#fff;box-shadow:0 3px 14px rgba(0,0,0,.1);text-align:center}
.card .jar{width:146px;height:206px;margin:16px auto 0;border-radius:40px 40px 34px 34px;background:linear-gradient(180deg,#111 0%,#222 26%,#6a0f0f 27%,#9b1d15 60%,#c0391d 85%,#5a0c0c 100%)}
.card h3{font-size:16px;font-weight:600;margin-top:26px}
.card .price{font-size:16px;color:var(--yellow)}
.card .price s{font-size:11px}
.card .add{display:block;width:158px;height:44px;margin:8px auto 0;border:2px solid var(--red);border-radius:22px;color:var(--red);font-weight:600;font-size:14px;line-height:40px}

.deals{left:0;top:1697px;width:1200px;height:498px;background:linear-gradient(135deg,#b8262c,#d0363c 50%,#b12228)}
.deals .ghost{position:absolute;font-size:80px;font-weight:700;color:rgba(255,255,255,.18);writing-mode:vertical-rl}
.deal-card{position:absolute;left:250px;top:85px;width:702px;height:310px;background:#fff;border-radius:40px 0 0 40px}
.deal-card small{position:absolute;left:242px;top:56px;font-size:12px;color:var(--red)}
.deal-card h2{position:absolute;left:76px;top:76px;font-size:46px;font-weight:500;letter-spacing:1px}
.deal-card p{position:absolute;left:70px;top:148px;width:316px;text-align:right;font-size:14px;line-height:30px}
.deal-card .btn{position:absolute;left:223px;top:213px;width:158px;height:42px;border:2px solid var(--red);border-radius:21px;color:var(--red);font-size:14px;font-weight:600;text-align:center;line-height:38px}
.deal-card .jar{position:absolute;left:462px;top:17px;width:195px;height:270px;border-radius:50px 50px 40px 40px;background:linear-gradient(180deg,#111 0%,#222 24%,#6a0f0f 25%,#a01f15 60%,#5a0c0c 100%)}
.dots{position:absolute;left:582px;top:427px;display:flex;gap:6px}
.dots i{width:7px;height:7px;border-radius:50%;background:#fff}
.dots i.on{background:var(--yellow)}

.reviews{left:0;top:2818px;width:1200px;height:420px;background:var(--grey)}
.reviews p{position:absolute;left:170px;top:160px;width:860px;text-align:center;font-size:13px;font-style:italic;line-height:30px;color:#333}
.reviews .name{position:absolute;left:0;width:1200px;top:278px;text-align:center;color:var(--red);font-weight:600;font-size:15px}
.reviews .rdots{position:absolute;left:1055px;top:168px}
.reviews .rdots i{display:block;width:9px;height:9px;border-radius:50%;background:#888;margin-bottom:18px}
.reviews .rdots i.on{background:var(--yellow)}

.footer{left:0;top:3160px;width:1200px;height:625px}
.mail-title{position:absolute;left:0;width:1160px;top:135px;text-align:center;color:#fff;font-size:33px;font-weight:700}
.mail-sub{position:absolute;left:0;width:1160px;top:190px;text-align:center;color:#fff;font-size:12px}
.mail-form{position:absolute;left:261px;top:238px;width:641px;height:48px;background:#fff;border-radius:24px}
.mail-form span{position:absolute;left:47px;top:15px;font-size:13px;color:#aaa}
.mail-form b{position:absolute;right:3px;top:3px;width:153px;height:42px;background:var(--red);border-radius:21px;color:#fff;font-size:15px;text-align:center;line-height:42px}
.rule{position:absolute;left:111px;top:320px;width:977px;height:1px;background:#555}
.fbrand{position:absolute;left:105px;top:378px;font-size:26px;font-weight:700;color:var(--red)}
.fsocial{position:absolute;left:83px;top:482px;display:flex;gap:13px}
.fsocial i{width:33px;height:33px;border-radius:50%;background:var(--yellow)}
.fcol{position:absolute;top:360px;color:#fff}
.fcol h4{font-size:15px;font-weight:600;margin-bottom:10px}
.fcol li{list-style:none;font-size:14px;line-height:30px;padding-left:12px}
.fcol li::before{content:"» ";}
.fcol .contact{font-size:14px;line-height:30px}
.bottom-rule{position:absolute;left:60px;top:552px;width:1068px;height:1px;background:#555}
.copy{position:absolute;left:67px;top:574px;color:#fff;font-size:11px}
.cards{position:absolute;left:874px;top:572px;display:flex;gap:6px}
.cards i{width:29px;height:18px;background:#e5e5e5;border-radius:2px}
</style>
</head>
<body>

<div class="abs topbar">
  <div class="left">USD &nbsp;| ENG &nbsp;| MY ACCOUNT</div>
  <div class="right">WORKING TIME: MON - SAT: 8:00 - 21:00</div>
</div>

<header class="abs header">
  <div class="brand">Chomp-iZ</div>
  <div class="search"><span>Type Here</span><b>SEARCH</b></div>
  <div class="call">
    <div class="ico">
      <svg width="52" height="52" viewBox="0 0 52 52"><path d="M19 16c2-1 3 0 4 3l1 3c0 1-1 2-2 3 1 3 3 5 6 6 1-1 2-2 3-2l3 1c3 1 4 2 3 4-1 3-3 4-6 3-7-2-12-7-14-14-1-3 0-5 2-7z" fill="var(--red)"/></svg>
    </div>
    <small>Call Us Today</small>
    <strong>123 456 7890</strong>
  </div>
</header>

<nav class="abs nav">
  <ul>
    <li class="active">HOME</li><li>ABOUT US</li><li>RECIPES</li><li>BUY NOW</li><li>EVENTS</li><li>CONTACT US</li>
  </ul>
  <div class="social">
    <i></i><i></i>
    <i><svg width="36" height="36" viewBox="0 0 36 36"><path d="M18 25l-6-6c-2-2-2-5 0-6 2-1 4 0 6 2 2-2 4-3 6-2 2 1 2 4 0 6z" fill="var(--red)"/></svg></i>
    <i><svg width="36" height="36" viewBox="0 0 36 36"><path d="M10 12h3l2 9h9l2-7H14" fill="none" stroke="var(--red)" stroke-width="2"/><circle cx="16" cy="24" r="1.5" fill="var(--red)"/><circle cx="23" cy="24" r="1.5" fill="var(--red)"/></svg></i>
  </div>
</nav>

<section class="abs hero" role="img" aria-label="Three jars of salsa on a table in front of a brick wall">
  <h1>Lorem ipsum dolor sit amet, consectetur<br>adipiscing elit sed do.</h1>
  <div class="btn">SHOP NOW</div>
  <div class="jars" role="img" aria-label="Mild, medium and hot salsa jars"></div>
  <svg class="abs" style="left:50px;top:242px" width="24" height="40" viewBox="0 0 24 40"><path d="M20 4L4 20l16 16" fill="none" stroke="#fff" stroke-width="2.5"/></svg>
  <svg class="abs" style="left:1124px;top:248px" width="24" height="40" viewBox="0 0 24 40"><path d="M4 4l16 16L4 36" fill="none" stroke="#fff" stroke-width="2.5"/></svg>
</section>

<section class="abs perks">
  <div class="perk" style="left:-12px">
    <svg width="56" height="42" viewBox="0 0 56 42"><rect x="6" y="4" width="30" height="24" fill="none" stroke="var(--red)" stroke-width="2"/><path d="M36 12h9l6 8v8H36" fill="none" stroke="var(--red)" stroke-width="2"/><circle cx="16" cy="32" r="4" fill="none" stroke="var(--red)" stroke-width="2"/><circle cx="44" cy="32" r="4" fill="none" stroke="var(--red)" stroke-width="2"/></svg>
    <b>FREE SHIPPING</b><span>On all orders over $75.00</span>
  </div>
  <div class="perk" style="left:240px">
    <svg width="56" height="42" viewBox="0 0 56 42"><path d="M18 8l14-6 14 6v16l-14 6-14-6z" fill="none" stroke="var(--red)" stroke-width="2"/><path d="M18 8l14 6 14-6M32 14v16" fill="none" stroke="var(--red)" stroke-width="2"/><circle cx="18" cy="30" r="8" fill="#fff" stroke="var(--red)" stroke-width="2"/></svg>
    <b>FREE FREE RETURNS</b><span>Returns are free within 9 days</span>
  </div>
  <div class="perk" style="left:500px">
    <svg width="56" height="42" viewBox="0 0 56 42"><rect x="6" y="2" width="44" height="30" rx="2" fill="none" stroke="var(--red)" stroke-width="2"/><path d="M6 10h44" stroke="var(--red)" stroke-width="2"/><path d="M28 18l6 3v5c0 4-3 6-6 8-3-2-6-4-6-8v-5z" fill="#fff" stroke="var(--red)" stroke-width="2"/></svg>
    <b>100% PAYMENT SECURE</b><span>Your payment are safe with us.</span>
  </div>
  <div class="perk" style="left:752px">
    <svg width="56" height="42" viewBox="0 0 56 42"><circle cx="26" cy="24" r="16" fill="none" stroke="var(--red)" stroke-width="2"/><text x="26" y="29" font-size="13" text-anchor="middle" fill="var(--red)" font-family="Poppins,sans-serif">24</text><rect x="34" y="2" width="14" height="10" rx="2" fill="none" stroke="var(--red)" stroke-width="2"/></svg>
    <b>SUPPORT 24/7</b><span>Contact us 24 hours a day</span>
  </div>
</section>

<h2 class="abs section-title" style="top:1148px">Our Featured <b>Products</b></h2>

<div class="card" style="left:172px;top:1243px"><div class="jar" role="img" aria-label="Mild salsa jar"></div><h3>Product Name</h3><div class="price">$129.00 <s>$200.00</s></div><a class="add">Add to Cart</a></div>
<div class="card" style="left:477px;top:1243px"><div class="jar" role="img" aria-label="Medium salsa jar"></div><h3>Product Name</h3><div class="price">$129.00 <s>$200.00</s></div><a class="add">Add to Cart</a></div>
<div class="card" style="left:781px;top:1243px"><div class="jar" role="img" aria-label="Hot salsa jar"></div><h3>Product Name</h3><div class="price">$129.00 <s>$200.00</s></div><a class="add">Add to Cart</a></div>

<section class="abs deals" role="img" aria-label="Red tinted photo of a salsa stand">
  <div class="ghost" style="left:82px;top:130px;transform:rotate(180deg)">BEST</div>
  <div class="ghost" style="left:1030px;top:90px">OFFERS</div>
  <div class="deal-card">
    <small>DEALS OF THE WEEK</small>
    <h2>SALE OFF 20%</h2>
    <p>Lorem ipsum dolor sit amet, consectetur adipiscing elit, sed do ei</p>
    <div class="btn">Shop Now</div>
    <div class="jar" role="img" aria-label="Hot salsa jar"></div>
  </div>
  <div class="dots"><i></i><i class="on"></i><i></i></div>
</section>

<h2 class="abs section-title" style="top:2270px">Our Bestsellers <b>Products</b></h2>

<div class="card" style="left:172px;top:2364px"><div class="jar" role="img" aria-label="Mild salsa jar"></div><h3>Product Name</h3><div class="price">$129.00 <s>$200.00</s></div><a class="add">Add to Cart</a></div>
<div class="card" style="left:477px;top:2364px"><div class="jar" role="img" aria-label="Medium salsa jar"></div><h3>Product Name</h3><div class="price">$129.00 <s>$200.00</s></div><a class="add">Add to Cart</a></div>
<div class="card" style="left:781px;top:2364px"><div class="jar" role="img" aria-label="Hot salsa jar"></div><h3>Product Name</h3><div class="price">$129.00 <s>$200.00</s></div><a class="add">Add to Cart</a></div>

<section class="abs reviews">
  <h2 class="abs section-title" style="top:70px">Our Customers <b>Reviews</b></h2>
  <p>Lorem ipsum dolor sit amet, consectetur adipiscing elit, sed do eiusmod tempor incididunt ut labore et dolore magna aliqua. Quis ipsum suspendisse ultrices gravida. Risus commodo viverra maecenas accumsan lacus vel facilisis.Ut enim ad minim veniam, quis nostrud exercitation ullamco laboris nisi ut aliquip ex ea commodo consequat. Duis aute irure dolor in reprehenderit in voluptate velit.</p>
  <div class="name">MARISOL</div>
  <div class="rdots"><i></i><i class="on"></i><i></i></div>
</section>

<footer class="abs footer">
  <svg class="abs" style="left:0;top:0" width="1200" height="625" viewBox="0 0 1200 625">
    <path d="M0 75 C200 0 420 20 600 70 C800 125 1000 40 1200 62 V625 H0Z" fill="var(--yellow)"/>
    <path d="M0 82 C200 10 420 30 600 80 C800 135 1000 50 1200 72 V625 H0Z" fill="var(--black)"/>
  </svg>
  <div class="mail-title">JOIN OUR MAILING LIST</div>
  <div class="mail-sub">Lorem ipsum dolor sit amet, consectetur adipiscing elit, sed do eiusmod tempor</div>
  <div class="mail-form"><span>Enter Email Here</span><b>SUBSCRIBE</b></div>
  <div class="rule"></div>
  <div class="fbrand">Chomp-iZ</div>
  <div class="fsocial"><i></i><i></i><i></i><i></i></div>
  <div class="fcol" style="left:314px"><h4>QUICK LINKS</h4><ul><li>Home</li><li>About Us</li><li>Recipes</li><li>Buy Now</li><li>Events</li></ul></div>
  <div class="fcol" style="left:532px"><h4>LEGAL</h4><ul><li>Privacy Policy</li><li>Terms &amp; Conditions</li><li>Contact Us</li><li>Cookie Policy</li></ul></div>
  <div class="fcol" style="left:771px"><h4>CONTACT US</h4>
    <div class="contact">
      <svg width="10" height="13" viewBox="0 0 10 13" style="margin:0 10px 0 10px"><path d="M5 0a5 5 0 0 1 5 5c0 3-5 8-5 8S0 8 0 5a5 5 0 0 1 5-5z" fill="#fff"/><circle cx="5" cy="5" r="2" fill="#000"/></svg>123 Lorem ipsum dolor sit amet<br><span style="padding-left:36px">consectetur adipisci.</span><br>
      <div style="margin-top:8px"><svg width="12" height="12" viewBox="0 0 12 12" style="margin:0 10px 0 10px"><path d="M2 1c1 0 2 2 2 3L3 5c1 2 2 3 4 4l1-1c1 0 3 1 3 2s-1 2-2 2C5 12 0 7 0 3c0-1 1-2 2-2z" fill="#fff"/></svg>123 456 7890</div>
      <div style="margin-top:14px"><svg width="13" height="10" viewBox="0 0 13 10" style="margin:0 10px 0 10px"><rect width="13" height="10" fill="#fff"/><path d="M0 0l6.5 5L13 0" fill="none" stroke="#000"/></svg>hello@chompizsalsa.com</div>
    </div>
  </div>
  <div class="bottom-rule"></div>
  <div class="copy">© Copyrights 2021 Chomp-iZ Salsa &nbsp;| &nbsp; All Rights Reserved</div>
  <div class="cards"><i></i><i></i><i></i><i></i></div>
</footer>

</body>
</html>
```